Small Business Broker Business Card Design

A business card design for a small business brokerage, which is a financial service, not unlike real estate brokerage, but for small businesses such as laundromats, pizza shops, restaurants, cleaners etc. The designs should all be simple, more conservative in nature, using the colors and font of the logo. Again, think real estate Brokerage as a business context
Contact Information for Business Card
Name: Glen R. Harlow. Title: Small Business Advisor. Email: g.harlow@bayfieldcapitalworks.example. Mobile: (555) 274-3918. Office: (555) 806-2147. www.bayfieldcapitalworks.example

```html
<!DOCTYPE html>
<html lang="en">
<head>
<meta charset="utf-8">
<title>Bayfield Capital Works – Business Card</title>
<link rel="stylesheet" href="https://fonts.googleapis.com/css2?family=Montserrat:wght@700&family=Open+Sans:wght@400;600;700&display=swap">
<style>
  :root {
    --navy: #1b3a6b;
    --green: #8cc63f;
    --ink: #1e1e1e;
    --paper: #ffffff;
    --backdrop: #232323;
  }
  * { box-sizing: border-box; margin: 0; padding: 0; }
  html, body { width: 1200px; height: 780px; overflow: hidden; }
  body {
    background: var(--backdrop);
    font-family: "Open Sans", Arial, sans-serif;
    position: relative;
  }
  .card {
    position: absolute;
    top: 230px;
    width: 560px;
    height: 320px;
    border-radius: 18px;
    overflow: hidden;
  }
  .card--front {
    left: 26px;
    background: linear-gradient(170deg, var(--navy) 0%, #3f6a64 45%, var(--green) 100%);
    display: flex;
    align-items: center;
    justify-content: center;
  }
  .card--back { left: 614px; background: var(--paper); }

  .brand {
    display: flex;
    align-items: center;
    gap: 8px;
    font-family: "Montserrat", Arial, sans-serif;
    font-weight: 700;
    text-transform: uppercase;
    white-space: nowrap;
  }
  .brand__mark { display: block; flex: none; }
  .card--front .brand { font-size: 24px; letter-spacing: 0.04em; color: var(--paper); gap: 10px; }
  .card--front .brand__mark { width: 22px; height: 22px; background: var(--paper); }
  .card--back .brand {
    position: absolute; left: 26px; top: 128px;
    font-size: 12px; letter-spacing: 0.02em; color: var(--navy);
  }
  .card--back .brand__mark { width: 13px; height: 13px; background: var(--green); }

  .divider {
    position: absolute; left: 306px; top: 60px;
    width: 1.5px; height: 130px; background: var(--green);
  }
  .contact { position: absolute; left: 322px; top: 48px; width: 230px; }
  .contact__name {
    font-weight: 700; font-size: 27px; line-height: 1.1; letter-spacing: -0.01em; white-space: nowrap;
  }
  .contact__first { color: var(--green); }
  .contact__last { color: var(--navy); }
  .contact__title { font-weight: 600; font-size: 13px; color: var(--ink); margin-top: 2px; }
  .contact__list { list-style: none; margin-top: 14px; }
  .contact__list li {
    display: flex; align-items: center; gap: 6px;
    font-size: 10.5px; color: var(--ink); line-height: 1.75; white-space: nowrap;
  }
  .contact__list svg { width: 11px; height: 11px; flex: none; }

  .address {
    position: absolute; left: 130px; top: 204px;
    font-size: 14px; color: var(--ink); white-space: nowrap;
  }
  .bands { position: absolute; left: 0; bottom: 0; width: 560px; height: 90px; }
</style>
</head>
<body>

  <section class="card card--front">
    <div class="brand"><span class="brand__mark"></span>Bayfield Capital Works, Inc</div>
  </section>

  <section class="card card--back">
    <div class="brand"><span class="brand__mark"></span>Bayfield Capital Works, Inc</div>

    <div class="divider"></div>

    <div class="contact">
      <p class="contact__name"><span class="contact__first">Glen R.</span> <span class="contact__last">Harlow</span></p>
      <p class="contact__title">Small Business Advisor</p>
      <ul class="contact__list">
        <li>
          <svg viewBox="0 0 24 24" aria-hidden="true"><path fill="#8cc63f" d="M6.6 10.8a15 15 0 0 0 6.6 6.6l2.2-2.2a1 1 0 0 1 1-.25 11.4 11.4 0 0 0 3.6.57 1 1 0 0 1 1 1V20a1 1 0 0 1-1 1A17 17 0 0 1 3 4a1 1 0 0 1 1-1h3.5a1 1 0 0 1 1 1c0 1.25.2 2.46.57 3.6a1 1 0 0 1-.25 1z"/></svg>
          (555) 274-3918
        </li>
        <li>
          <svg viewBox="0 0 24 24" aria-hidden="true"><rect x="2" y="5" width="20" height="14" rx="2" fill="#8cc63f"/><path d="M3 6l9 7 9-7" fill="none" stroke="#fff" stroke-width="2"/></svg>
          g.harlow@bayfieldcapitalworks.example
        </li>
        <li>
          <svg viewBox="0 0 24 24" aria-hidden="true"><circle cx="12" cy="12" r="10" fill="#8cc63f"/><path d="M2 12h20M12 2c3 3 3 17 0 20M12 2c-3 3-3 17 0 20" fill="none" stroke="#fff" stroke-width="1.5"/></svg>
          www.bayfieldcapitalworks.example
        </li>
      </ul>
    </div>

    <p class="address">4180 Lakeside Ave. Suite 210 Bayfield, TX 75019</p>

    <svg class="bands" viewBox="0 0 560 90" preserveAspectRatio="none" aria-hidden="true">
      <polygon points="380,58 560,18 560,90 410,90" fill="var(--navy)"/>
      <polygon points="0,80 340,48 366,48 388,90 0,90" fill="var(--green)"/>
    </svg>
  </section>

</body>
</html>
```